Business Card for Lantern Reach

Please design a Modern Business card for a Online Marketing Company

Website: http://www.lanternreach-example.com.au

Please do NOT include physical address in design.

```html
<!DOCTYPE html>
<html lang="en">
<head>
<meta charset="utf-8">
<title>Lantern Reach – Business Card</title>
<link rel="stylesheet" href="https://fonts.googleapis.com/css2?family=Roboto:wght@400;700;900&family=Roboto+Condensed:wght@400;700&display=swap">
<style>
  :root {
    --board: #8a8a8a;
    --paper: #ffffff;
    --brand-red: #b3222c;
    --ink: #1a1a1a;
    --accent: #e8402a;
    --rule: #f5c7a4;
    --back-top: #f36f35;
    --back-bottom: #ee3d3b;
    --white: #ffffff;
    --icon: rgba(255,255,255,0.45);
  }
  * { box-sizing: border-box; margin: 0; padding: 0; }
  html, body { width: 983px; height: 1200px; overflow: hidden; }
  body {
    background: var(--board);
    position: relative;
    font-family: "Roboto", Arial, sans-serif;
  }
  .card {
    position: absolute;
    left: 31px;
    width: 903px;
    height: 539px;
    box-shadow: 10px 10px 0 rgba(0,0,0,0.55);
    overflow: hidden;
  }
  /* Front */
  .card--front { top: 36px; background: var(--paper); }
  .front__pattern {
    position: absolute; left: 0; top: 0; width: 100%; height: 130px;
    background: linear-gradient(180deg, rgba(246,196,170,0.35), rgba(255,255,255,0));
  }
  .brand { position: absolute; left: 110px; top: 200px; display: flex; align-items: center; gap: 40px; }
  .brand__square { width: 120px; height: 120px; background: var(--brand-red); flex: none; }
  .brand__name {
    font-family: "Roboto", Arial, sans-serif;
    font-weight: 900; font-size: 62px; line-height: 1;
    color: var(--brand-red); letter-spacing: 0.5px; text-transform: uppercase;
  }
  .brand__tagline {
    margin-top: 10px; text-align: center;
    font-weight: 700; font-size: 27px; color: var(--ink);
  }
  .front__rule {
    position: absolute; left: 52px; right: 52px; top: 447px;
    height: 2px; background: var(--rule);
  }
  .front__contacts {
    position: absolute; left: 52px; right: 52px; top: 473px;
    display: flex; justify-content: space-between;
    font-family: "Roboto Condensed", Arial, sans-serif;
    font-size: 20px; color: var(--accent);
  }
  /* Back */
  .card--back {
    top: 611px;
    background: linear-gradient(180deg, var(--back-top) 0%, var(--back-bottom) 100%);
    color: var(--white);
    font-family: "Roboto Condensed", Arial, sans-serif;
  }
  .person { position: absolute; left: 356px; top: 92px; white-space: nowrap; line-height: 1; }
  .person__name { font-size: 76px; font-weight: 400; }
  .person__title { font-size: 30px; margin-left: 12px; }
  .back__contacts {
    position: absolute; right: 418px; top: 233px;
    text-align: right; font-size: 28px; font-weight: 700; line-height: 41px;
  }
  .social { position: absolute; left: 593px; top: 277px; display: flex; gap: 30px; }
  .social__dot { width: 30px; height: 30px; border-radius: 50%; background: var(--icon); }
  .back__pattern {
    position: absolute; left: 0; bottom: 0; width: 100%; height: 125px;
    background: linear-gradient(180deg, rgba(255,255,255,0) 0%, rgba(250,120,110,0.55) 45%, rgba(235,35,50,0.6) 100%);
  }
</style>
</head>
<body>
  <section class="card card--front">
    <div class="front__pattern" role="img" aria-label="Faint band of overlapping outlined squares"></div>
    <div class="brand">
      <div class="brand__square" aria-hidden="true"></div>
      <div>
        <div class="brand__name">Lantern Reach</div>
        <div class="brand__tagline">Shine online - Reach further</div>
      </div>
    </div>
    <div class="front__rule"></div>
    <div class="front__contacts">
      <span>plan@lanternreach-example.com.au</span>
      <span>0491 570 156</span>
      <span>lanternreach-example.com.au</span>
    </div>
  </section>

  <section class="card card--back">
    <div class="person">
      <span class="person__name">John Doe</span><span class="person__title">Position Title</span>
    </div>
    <div class="back__contacts">
      <div>plan@lanternreach-example.com.au</div>
      <div>lanternreach-example.com.au</div>
      <div>0491 570 156</div>
    </div>
    <div class="social" aria-hidden="true">
      <span class="social__dot"></span><span class="social__dot"></span><span class="social__dot"></span><span class="social__dot"></span><span class="social__dot"></span>
    </div>
    <div class="back__pattern" role="img" aria-label="Band of overlapping translucent rounded squares along the bottom edge"></div>
  </section>
</body>
</html>
```